Unique Realty Niche needs a web design

Starting Note: Please do not use the colors from the logo on quickhousebarnowl.net which is their current website. This logo will eventually change but it is what they have now.

This website is a realty website that caters to individuals who want to rent out their homes (investors) and those who want to rent a home (Tenants). We provide no credit check to rent a home from a investor at a higher cost for the tenant to balance risk. Good renters with bad credit are able to rent or buy a house from investors who are registered in our system.

Target Market(s)

Home Owners trying to rent out their homes, and people looking to rent.

Industry/Entity Type

House

Requirements
Must have
• Main Navigation links: Home - Our Story - tenant - owner - contact us

A log in form somewhere on the page.

Key themes in the site are as follows: The site needs to be clean and professional looking i.e. no grunge. I provided some color palettes below, these are not set in stone and if you know of a good palette(s) our client is very open to all suggestions. The main navigation needs to stay on top but other on page navigations could go on left (preferably) On the left or the right will be featured listings for some homes. It will be between 3 to 5 listings showing at one time. (Please see quickhousebarnowl.net for example)

Example Color Palettes:
http://hueplank.example.org/#themeID/1634353
http://hueplank.example.org/#themeID/166988
http://hueplank.example.org/#themeID/1638382
http://hueplank.example.org/#themeID/1677863

Example Websites That Client Likes:
NOTE: Very Flexible, no need to duplicate these below.
http://www.fernlotgroupvx.net/
http://www.tqbgrove.net/
http://www.wubalestewards.net/index.php?pr=Home_Page

Nice to have
• It would be nice to have short easy to read paragraphs accompanied by a photo so scanning is easy on the site. Then in later pages we will have more text when there is more detail needed. We know you wont come up with the content but concept would be nice.

```html
<!DOCTYPE html>
<html lang="en">
<head>
<meta charset="utf-8">
<title>Barn Owl House Buyers</title>
<link rel="stylesheet" href="https://fonts.googleapis.com/css2?family=Open+Sans:wght@400;600;700&display=swap">
<style>
:root{
  --paper:#fdf8f4;
  --ink:#2b2b2b;
  --brown:#5a4a42;
  --red:#b52a10;
  --red-hi:#e4461d;
  --band-top:#333;
  --band-bottom:#5a5a5a;
  --field:#3e3e3e;
  --frame:#555;
  --footer:#3c3c3c;
}
*{box-sizing:border-box;margin:0;padding:0}
html,body{width:1091px;height:1200px;overflow:hidden;background:var(--paper)}
body{font-family:"Open Sans",Arial,sans-serif;color:var(--ink)}
.page{position:relative;width:1000px;height:1100px;transform:scale(1.091);transform-origin:0 0;background:var(--paper)}
.abs{position:absolute}

/* header */
.brand{left:16px;top:40px;display:flex;align-items:center;gap:12px}
.brand-mark{width:40px;height:40px;border-radius:50%;background:var(--brown)}
.brand-name{font-size:23px;font-weight:700;color:var(--brown);letter-spacing:-.2px;white-space:nowrap}
.main-nav a{position:absolute;top:58px;font-size:15px;color:#4a3a32;text-decoration:none;white-space:nowrap}
.main-nav .active{left:508px;top:0;width:92px;height:100px;padding-top:58px;text-align:center;color:#fff;
  background:linear-gradient(#e8481e,#a8230e);box-shadow:0 3px 5px rgba(0,0,0,.35)}

/* log-in */
.login{left:620px;top:116px;display:flex;align-items:center;gap:8px;font-size:12px;color:#4a3a32}
.login .input{width:112px;height:22px;background:#ece5de;border:1px solid #d3c9bf;color:#8a7d74;font-size:11px;line-height:20px;padding:0 7px}
.login .go-btn{width:56px;height:22px;background:var(--red);color:#fff;text-align:center;line-height:22px;font-size:12px}

/* feature band */
.band{left:0;top:152px;width:1000px;height:364px;border-top:2px solid #cfc6bd;border-bottom:2px solid #cfc6bd;
  background:linear-gradient(var(--band-top),var(--band-bottom))}
.listing{width:294px;height:293px;background:#fff;padding:4px}
.listing .photo{width:100%;height:285px}
.listing .go{position:absolute;right:-10px;bottom:-10px;width:31px;height:31px;border-radius:50%;background:#fff;box-shadow:0 1px 3px rgba(0,0,0,.4)}
.caption{font-size:12.5px;color:#fff;white-space:nowrap}
.band-arrow{top:306px}

/* search */
.search{left:742px;top:172px;width:243px;height:293px;background:var(--paper);border:1px solid #fff;box-shadow:0 0 0 1px #ccc inset}
.search h2{position:absolute;left:50px;top:12px;font-size:19px;font-weight:400;color:#333;white-space:nowrap}
.search label{position:absolute;font-size:12.5px;color:#333}
.field{position:absolute;background:var(--field);height:21px}
.field.select::after{content:"";position:absolute;right:8px;top:8px;border:5px solid transparent;border-top-color:#fff}
.search .btn{position:absolute;left:141px;top:245px;width:85px;height:24px;border-radius:4px;background:#c9553a;color:#fff;font-size:13px;text-align:center;line-height:24px}
.adv{left:863px;top:482px;font-size:12.5px;color:#fff;text-decoration:underline}

/* content */
.section-title{font-size:19px;font-weight:400;color:#333}
.view-all{left:649px;top:546px;font-size:13px;color:#333}
.thumb{width:161px;height:92px;border:3px solid var(--frame)}
.thumb div{height:100%}
.testimonial{width:321px;font-size:12.5px;line-height:18px}
.testimonial p{text-align:justify}
.testimonial .more{display:block;text-align:right;color:var(--red);margin-top:8px;padding-right:2px}

/* side */
.mail{left:726px;top:585px;width:258px;height:42px;background:#4a4646;color:#fff;font-size:12px;padding:13px 18px}
.submit{left:906px;top:636px;width:78px;height:32px;background:var(--red);color:#fff;font-size:14px;text-align:center;line-height:32px}
.contact-row{font-size:12.5px;line-height:22px;display:flex}
.contact-row dt{width:72px;text-align:right;padding-right:10px;white-space:nowrap}
.contact-row dd{white-space:nowrap}
.social{left:728px;top:994px;display:flex;gap:18px}
.social span{width:22px;height:22px;border-radius:3px}

/* footer */
.footer{left:0;top:1035px;width:1000px;height:65px;background:var(--footer);color:#fff;font-size:13px}
.footer a{position:absolute;top:24px;color:#fff;text-decoration:none;white-space:nowrap}
</style>
</head>
<body>
<div class="page">

  <header>
    <div class="abs brand"><span class="brand-mark"></span><span class="brand-name">BARN OWL HOUSE BUYERS</span></div>
    <nav class="main-nav">
      <a class="active" href="#">Home</a>
      <a style="left:615px" href="#">Our Story</a>
      <a style="left:723px" href="#">Tenant</a>
      <a style="left:811px" href="#">Owner</a>
      <a style="left:896px" href="#">Contact us</a>
    </nav>
    <form class="abs login" aria-label="Member log in">
      <span class="input">Username</span>
      <span class="input">Password</span>
      <span class="go-btn">Log in</span>
    </form>
  </header>

  <section class="abs band" aria-label="Featured listings"></section>
  <svg class="abs band-arrow" style="left:24px" width="18" height="26" viewBox="0 0 18 26"><path d="M14 2 4 13l10 11" fill="none" stroke="#fff" stroke-width="3"/></svg>
  <svg class="abs band-arrow" style="left:694px" width="18" height="26" viewBox="0 0 18 26"><path d="M4 2l10 11L4 24" fill="none" stroke="#fff" stroke-width="3"/></svg>

  <div class="abs listing" style="left:62px;top:172px">
    <div class="photo" role="img" aria-label="Cream two-storey townhouses under blue sky" style="background:linear-gradient(#6ea9dc 0%,#cfe0ee 45%,#e8dcbc 60%,#7b7b7b 100%)"></div>
    <svg class="go" viewBox="0 0 31 31"><path d="M13 10l5 5.5-5 5.5" fill="none" stroke="#333" stroke-width="2"/></svg>
  </div>
  <div class="abs listing" style="left:382px;top:172px">
    <div class="photo" role="img" aria-label="Stone-faced suburban house with lawn" style="background:linear-gradient(#4f8fd6 0%,#a8c4e0 40%,#b8a892 60%,#4f9a2e 85%,#3c7a22 100%)"></div>
    <svg class="go" viewBox="0 0 31 31"><path d="M13 10l5 5.5-5 5.5" fill="none" stroke="#333" stroke-width="2"/></svg>
  </div>
  <p class="abs caption" style="left:72px;top:482px">1409 Quillmoor Lane Ferndale, TX 75990</p>
  <p class="abs caption" style="left:392px;top:482px">1409 Quillmoor Lane Ferndale, TX 75990</p>

  <form class="abs search">
    <svg class="abs" style="left:12px;top:10px" width="30" height="32" viewBox="0 0 30 32"><circle cx="13" cy="13" r="10" fill="#8cc6ee" stroke="#3a86c4" stroke-width="2"/><path d="M20 21l7 8" stroke="#555" stroke-width="4" stroke-linecap="round"/></svg>
    <h2>Property Search</h2>
    <label style="left:16px;top:59px">Price Range</label>
    <span class="field" style="left:16px;top:83px;width:88px"></span>
    <label style="left:114px;top:85px;color:#999">to</label>
    <span class="field" style="left:137px;top:83px;width:88px"></span>
    <label style="left:16px;top:117px">Location</label>
    <span class="field select" style="left:16px;top:141px;width:209px"></span>
    <label style="left:16px;top:177px">Availability</label>
    <label style="left:137px;top:177px">Furnished</label>
    <span class="field select" style="left:16px;top:201px;width:88px"></span>
    <span class="field select" style="left:137px;top:201px;width:88px"></span>
    <span class="btn">Search</span>
  </form>
  <a class="abs adv" href="#">Advanced Search</a>

  <h2 class="abs section-title" style="left:12px;top:540px">Proposals</h2>
  <a class="abs view-all">View all</a>
  <div class="abs thumb" style="left:12px;top:585px" role="img" aria-label="Mediterranean villa"><div style="background:linear-gradient(#78b0e0,#d8b488 55%,#6a9040)"></div></div>
  <div class="abs thumb" style="left:186px;top:585px" role="img" aria-label="White colonial house among trees"><div style="background:linear-gradient(#3f6e2e,#e8e8e2 55%,#5b9a38)"></div></div>
  <div class="abs thumb" style="left:361px;top:585px" role="img" aria-label="Farmhouse on a green hill"><div style="background:linear-gradient(#6fa8e0,#d8d4c4 55%,#6aa83c)"></div></div>
  <div class="abs thumb" style="left:535px;top:585px" role="img" aria-label="Modern office building"><div style="background:linear-gradient(90deg,#6fa0d8,#e0ddd4 40%,#5a6068)"></div></div>
  <div class="abs thumb" style="left:12px;top:689px" role="img" aria-label="Resort pool with palm trees"><div style="background:linear-gradient(#4a90e0,#f0f0f0 45%,#2cb4e8)"></div></div>
  <div class="abs thumb" style="left:186px;top:689px" role="img" aria-label="Yellow hacienda courtyard"><div style="background:linear-gradient(#c89a2c,#d4a848 50%,#4e8a30)"></div></div>
  <div class="abs thumb" style="left:361px;top:689px" role="img" aria-label="Seaside terrace with white chairs"><div style="background:linear-gradient(#5a98d8,#3a7ab0 55%,#e6e6e6)"></div></div>
  <div class="abs thumb" style="left:535px;top:689px" role="img" aria-label="Stone cottage with lawn"><div style="background:linear-gradient(#5a8a40,#d8d0c4 50%,#5a9038)"></div></div>

  <h2 class="abs section-title" style="left:12px;top:811px">Testimonials</h2>
  <div class="abs testimonial" style="left:12px;top:853px">
    <p style="margin-bottom:15px">Cicero are also reproduced in their exact original</p>
    <p>Lorem Ipsum as their default model text, and a search for will uncover many web sites still in their infancy. Various versions have evolved over the years, sometimes by accident.</p>
    <span class="more">View more...</span>
  </div>
  <div class="abs testimonial" style="left:363px;top:853px">
    <p style="margin-bottom:15px">Cicero are also reproduced in their exact original</p>
    <p>Lorem Ipsum as their default model text, and a search for will uncover many web sites still in their infancy. Various versions have evolved over the years, sometimes by accident.</p>
    <span class="more">View more...</span>
  </div>

  <h2 class="abs section-title" style="left:725px;top:540px">News Letter</h2>
  <div class="abs mail">Enter mail ID</div>
  <div class="abs submit">SUBMIT</div>

  <h2 class="abs section-title" style="left:725px;top:686px">Contact Us</h2>
  <dl class="abs" style="left:713px;top:729px">
    <div class="contact-row"><dt>Address :</dt><dd>Finibus Bonorum<br>Cicero reproduced<br>Accompanied<br>English</dd></div>
    <div class="contact-row" style="margin-top:20px"><dt>Phone :</dt><dd>258 555 0148</dd></div>
    <div class="contact-row" style="margin-top:21px"><dt>Fax :</dt><dd>258 555 0198</dd></div>
    <div class="contact-row" style="margin-top:21px"><dt>Email :</dt><dd>info@bohb.net</dd></div>
  </dl>
  <p class="abs" style="left:727px;top:966px;font-size:12.5px">Connect with us :</p>
  <div class="abs social" aria-label="Social links">
    <span style="background:#3b5b98"></span><span style="background:#5cc2ec"></span><span style="background:#f06a22"></span><span style="background:#1a6ea6"></span><span style="background:#55a845"></span>
  </div>

  <footer class="abs footer">
    <a style="left:13px" href="#">Home</a>
    <a style="left:81px" href="#">Our Story</a>
    <a style="left:174px" href="#">Tenant</a>
    <a style="left:249px" href="#">Owner</a>
    <a style="left:322px" href="#">Contact us</a>
    <span class="abs" style="right:12px;top:24px;white-space:nowrap">Copyright © 2011 BOHB</span>
  </footer>
</div>
</body>
</html>
```